Building company buisness cards

We are looking for a sharp modern new look for our business cards.
We are a New Zealand based company that specialises in house and land packages.
We have attached a photo of the current logo and would like to see if it can be improved somehow if needed.
We are open to any colours but we have chosen green at this stage.
Feel free to change the font and make the logo smarter looking.
Play with the colours and see what looks best.

We want a card that looks so good know one will want to throw it away!

Target Market(s)

Home buyers

Industry/Entity Type

Building

Contact Information for Business Card

Derek Tolvane
0217394062
dtolvane@quillmarkhomesteads.co.nz
quillmarkhomesteads.co.nz

Font styles to use
Serif
Sans Serif

Colors

Designer to choose colors to be used in the design.

Requirements
Must have
• Logo and company name on one side, details on the other side
Nice to have
• Color codes for the original green are HEX #4a8028, RGB(74,128,40), CMYK(42,0,69,50)
• Round corners, Raised and/or spot UV

```html
<!DOCTYPE html>
<html lang="en">
<head>
<meta charset="utf-8">
<title>Quillmark Homesteads — Business Cards</title>
<link rel="stylesheet" href="https://fonts.googleapis.com/css2?family=Open+Sans:wght@400&family=Arimo:wght@400&display=swap">
<style>
  :root {
    --bg: #1b1b1b;
    --card: #050505;
    --green: #4a8028;
    --green-bright: #4f9a2a;
    --grey: #6e6e6e;
    --grey-light: #9a9a9a;
    --white: #f2f2f2;
  }
  * { margin: 0; padding: 0; box-sizing: border-box; }
  html, body { width: 1200px; height: 960px; overflow: hidden; background: var(--bg); }
  .stage { position: relative; width: 1200px; height: 960px; }

  .card {
    position: absolute;
    width: 525px; height: 300px;
    background: var(--card);
    border-radius: 10px;
    overflow: hidden;
    box-shadow: 0 18px 40px rgba(0,0,0,.55);
  }
  .card--front { left: 337px; top: 130px; }
  .card--back  { left: 337px; top: 500px; }

  .wordmark {
    display: flex; align-items: center; justify-content: center; gap: 10px;
    font-family: "Open Sans", sans-serif;
    font-weight: 400;
    color: var(--green-bright);
    white-space: nowrap;
  }
  .wordmark__sq { display: block; background: var(--green-bright); flex: none; }
  .rule { height: 1px; background: var(--green-bright); }

  /* front */
  .front__brand { position: absolute; left: 0; right: 0; top: 100px; }
  .front__brand .wordmark { font-size: 30px; }
  .front__brand .wordmark__sq { width: 16px; height: 16px; }
  .front__brand .rule { width: 110px; margin: 16px auto 0; }
  .front__url {
    position: absolute; left: 0; right: 0; top: 196px; text-align: center;
    font-family: "Open Sans", sans-serif; font-size: 15px; letter-spacing: 1.5px; color: var(--white);
  }
  .front__url .accent { color: var(--green-bright); }

  /* back */
  .back__brand { position: absolute; left: 30px; top: 30px; width: 250px; }
  .back__brand .wordmark { font-size: 20px; gap: 8px; }
  .back__brand .wordmark__sq { width: 11px; height: 11px; }
  .back__brand .rule { width: 84px; margin: 12px auto 0; }
  .back__person { position: absolute; left: 40px; top: 100px; font-family: "Arimo", sans-serif; line-height: 1.2; }
  .back__name { font-size: 20px; color: var(--green-bright); }
  .back__title { font-size: 18px; color: var(--white); }
  .back__wave { position: absolute; left: 0; top: 0; }
  .contact {
    position: absolute; right: 26px; bottom: 14px;
    font-family: "Open Sans", sans-serif; font-size: 12px; color: var(--white); line-height: 20px;
  }
  .contact__row { display: flex; justify-content: flex-end; align-items: center; gap: 6px; }
  .contact__icon { width: 11px; height: 11px; flex: none; }
</style>
</head>
<body>
<main class="stage">

  <section class="card card--front" aria-label="Card front">
    <div class="front__brand">
      <div class="wordmark"><span class="wordmark__sq"></span><span>Quillmark Homesteads</span></div>
      <div class="rule"></div>
    </div>
    <p class="front__url">www.<span class="accent">quillmarkhomesteads</span>.co.nz</p>
  </section>

  <section class="card card--back" aria-label="Card back">
    <svg class="back__wave" width="525" height="300" viewBox="0 0 525 300">
      <path d="M0,165 C120,195 240,200 340,188 C420,178 470,168 525,165 L525,300 L0,300Z" fill="var(--grey)"/>
      <path d="M0,176 C120,206 240,210 340,196 C420,187 470,176 525,172 L525,300 L0,300Z" fill="var(--card)"/>
      <path d="M0,182 C120,212 240,215 340,201 C420,192 470,182 525,178 L525,300 L0,300Z" fill="var(--grey-light)"/>
      <path d="M0,192 C120,220 240,222 340,208 C420,199 470,190 525,186 L525,300 L0,300Z" fill="var(--green)"/>
    </svg>

    <div class="back__brand">
      <div class="wordmark"><span class="wordmark__sq"></span><span>Quillmark Homesteads</span></div>
      <div class="rule"></div>
    </div>

    <div class="back__person">
      <p class="back__name">Derek Tolvane</p>
      <p class="back__title">Title</p>
    </div>

    <div class="contact">
      <div class="contact__row">
        <svg class="contact__icon" viewBox="0 0 12 12"><rect x="1" y="2.5" width="10" height="7" rx="1" fill="var(--white)"/><path d="M1.5 3 L6 6.5 L10.5 3" stroke="var(--green)" stroke-width="1" fill="none"/></svg>
        <span>dtolvane@quillmarkhomesteads.co.nz</span>
      </div>
      <div class="contact__row">
        <svg class="contact__icon" viewBox="0 0 12 12"><path d="M2.5 1 L4.5 1 L5.2 3.6 L4 4.6 C4.6 6 6 7.4 7.4 8 L8.4 6.8 L11 7.5 L11 9.5 C11 10.4 10.4 11 9.5 11 C5 11 1 7 1 2.5 C1 1.6 1.6 1 2.5 1Z" fill="var(--white)"/></svg>
        <span>0217394062</span>
      </div>
      <div class="contact__row">
        <svg class="contact__icon" viewBox="0 0 12 12"><circle cx="6" cy="6" r="5" fill="none" stroke="var(--white)" stroke-width="1.2"/><path d="M1 6 H11 M6 1 C3.5 3.5 3.5 8.5 6 11 M6 1 C8.5 3.5 8.5 8.5 6 11" stroke="var(--white)" stroke-width="1" fill="none"/></svg>
        <span>www.quillmarkhomesteads.co.nz</span>
      </div>
    </div>
  </section>

</main>
</body>
</html>
```